Business Card Design

We are a manufacturing and distribution company with most of our customer base being supermarkets. We have established brand guidelines that are attached.

```html
<!DOCTYPE html>
<html lang="en">
<head>
<meta charset="utf-8">
<title>Corvane Business Card</title>
<link href="https://fonts.googleapis.com/css2?family=Montserrat:wght@400;500;700;800&display=swap" rel="stylesheet">
<style>
  :root {
    --backdrop: #6a6a6a;
    --card: #ffffff;
    --brand-red: #ee1c25;
    --brand-red-light: #f4593f;
    --brand-blue: #1877d2;
    --brand-blue-light: #3a9be6;
    --ink: #111111;
    --muted: #666666;
  }
  * { margin: 0; padding: 0; box-sizing: border-box; }
  html, body {
    width: 1200px;
    height: 1056px;
    overflow: hidden;
    background: var(--backdrop);
    font-family: "Montserrat", Arial, sans-serif;
  }
  .sheet {
    position: relative;
    width: 1200px;
    height: 1056px;
  }
  .card {
    position: absolute;
    left: 180px;
    width: 840px;
    height: 480px;
    background: var(--card);
    overflow: hidden;
    box-shadow: 0 14px 30px rgba(0,0,0,0.28);
  }
  .card--front { top: 36px; }
  .card--back { top: 544px; }

  .wordmark {
    position: absolute;
    display: flex;
    align-items: center;
    gap: 14px;
    font-weight: 800;
    color: var(--ink);
    letter-spacing: 0.04em;
  }
  .wordmark__square {
    width: 26px;
    height: 26px;
    background: var(--brand-red);
  }
  .card--front .wordmark {
    left: 70px;
    top: 92px;
    font-size: 44px;
  }

  .person {
    position: absolute;
    right: 70px;
    top: 170px;
    text-align: right;
  }
  .person__name {
    font-size: 34px;
    font-weight: 700;
    letter-spacing: 0.01em;
  }
  .person__first { color: var(--brand-red); }
  .person__last { color: var(--brand-blue); font-weight: 500; }
  .person__title {
    font-size: 20px;
    color: var(--muted);
    letter-spacing: 0.06em;
    margin-top: 2px;
  }

  .band {
    position: absolute;
    left: 0;
    top: 262px;
    width: 840px;
    height: 140px;
  }
  .contacts {
    position: absolute;
    left: 56px;
    top: 282px;
    list-style: none;
    color: #ffffff;
    font-size: 21px;
    font-weight: 500;
  }
  .contacts li {
    display: flex;
    align-items: center;
    gap: 12px;
    height: 33px;
  }
  .contacts svg { width: 22px; height: 22px; flex: none; }

  .card--back .wordmark {
    left: 0;
    right: 0;
    top: 0;
    bottom: 0;
    justify-content: center;
    font-size: 66px;
    gap: 22px;
  }
  .card--back .wordmark__square { width: 40px; height: 40px; }
</style>
</head>
<body>
<main class="sheet">

  <section class="card card--front" aria-label="Business card front">
    <div class="wordmark"><span class="wordmark__square"></span>CORVANE</div>

    <div class="person">
      <div class="person__name"><span class="person__first">MARA</span> <span class="person__last">LINDEN</span></div>
      <div class="person__title">Manager</div>
    </div>

    <svg class="band" viewBox="0 0 840 140" preserveAspectRatio="none" aria-hidden="true">
      <defs>
        <linearGradient id="band-red" x1="0" x2="1" y1="0" y2="0">
          <stop offset="0" stop-color="var(--brand-red)"/>
          <stop offset="0.55" stop-color="var(--brand-red-light)"/>
          <stop offset="1" stop-color="var(--brand-red)"/>
        </linearGradient>
        <linearGradient id="band-blue" x1="0" x2="1" y1="0" y2="0">
          <stop offset="0" stop-color="var(--brand-blue)"/>
          <stop offset="0.5" stop-color="var(--brand-blue-light)"/>
          <stop offset="1" stop-color="var(--brand-blue)"/>
        </linearGradient>
      </defs>
      <polygon points="0,0 640,0 590,140 0,140" fill="url(#band-red)"/>
      <polygon points="650,0 840,0 840,140 600,140" fill="url(#band-blue)"/>
    </svg>

    <ul class="contacts">
      <li>
        <svg viewBox="0 0 24 24"><rect x="1" y="1" width="22" height="22" rx="4" fill="#fff"/><path d="M8 5l2.5 3-1.5 2a9 9 0 0 0 5 5l2-1.5 3 2.5-1.5 2.5c-6 0-12-6-12-12z" fill="var(--brand-red)"/></svg>
        (555) 014-2280
      </li>
      <li>
        <svg viewBox="0 0 24 24"><rect x="1" y="1" width="22" height="22" rx="4" fill="#fff"/><rect x="5" y="7" width="14" height="10" fill="none" stroke="var(--brand-red)" stroke-width="1.8"/><path d="M5 7l7 6 7-6" fill="none" stroke="var(--brand-red)" stroke-width="1.8"/></svg>
        info@corvanemail.com
      </li>
      <li>
        <svg viewBox="0 0 24 24"><rect x="1" y="1" width="22" height="22" rx="4" fill="#fff"/><path d="M9 5v13l3-3 2 5 2-1-2-5h4z" fill="var(--brand-red)"/></svg>
        www.corvane.com
      </li>
    </ul>
  </section>

  <section class="card card--back" aria-label="Business card back">
    <div class="wordmark"><span class="wordmark__square"></span>CORVANE</div>
  </section>

</main>
</body>
</html>
```